Killer Webpage Design

I currently have a self-hosted webpage through wordpress at www.velmarqstudio.com - the content is complete and I'm happy with this but I need it designed (no coding) to complete my requirements. I'm happy to take designs which are non-Wordpress if there is specific advantage in this.

My full branding logos are attached along with color files. My main aim is consistent branding across all areas (social media, business cards, emails, websites). I have the rest running but am not happy with the available default selections from Wordpress.

I would prefer to use the darker blue version of the logo as I feel this has more standout in online media, however I would appreciate submissions with both variants to help me choose.

With the homepage I will also want to see blog pages and category pages designed but this can come after I have selected a design to go with,

Sites that I like and are related to my business include the following:
http://www.brindlepath.com/au/accounting-software/
http://www.tasklanternpro.com/home.aspx
https://pelicoin.com/register
Updates

Apologies for the confusion - to clarify for designers I am looking for design only, no coding.

FYI - i have now uploaded business cards for an idea of the contemporary style of design completed so far.

Target Market(s)

small to medium business. Not systemised but looking for help and support.

Industry/Entity Type

Business

Requirements
Must have
• I'm looking for a minimalist professional page, with the ability to easily add new sections when required. I will also need a CMS to add blog posts on the go, with the same features that it currently has (comments, social logon etc)

```html
<!DOCTYPE html>
<html lang="en">
<head>
<meta charset="utf-8">
<title>Velmarq Studio</title>
<link href="https://fonts.googleapis.com/css2?family=Source+Sans+3:wght@400;600;700&display=swap" rel="stylesheet">
<style>
:root{
  --navy:#04202c;
  --navy-2:#0b3b4f;
  --teal:#1fb3c6;
  --teal-dark:#1492a6;
  --red:#a31d28;
  --orange:#d4601c;
  --orange-light:#e8792e;
  --text:#2b2b2b;
  --link:#1c5a82;
  --paper:#ffffff;
  --grey-band:#ececec;
  --footer:#2a2a2a;
}
*{box-sizing:border-box;margin:0;padding:0}
html,body{width:908px;height:1200px;overflow:hidden}
body{font-family:"Source Sans 3",sans-serif;color:var(--text);background:var(--paper);position:relative}
.abs{position:absolute}
.header{left:0;top:0;width:908px;height:90px;background:linear-gradient(#062634,#031a24)}
.brand{left:77px;top:24px;display:flex;align-items:center;gap:10px;color:#fff;font-size:26px;font-weight:600}
.brand-dot{width:34px;height:34px;border-radius:50%;background:var(--teal)}
.search{left:610px;top:34px;width:160px;height:22px;background:#fff;border:1px solid #ccc;font-size:11px;color:#666;padding:3px 12px;display:flex;justify-content:space-between;align-items:center}
.lang{left:776px;top:34px;width:65px;height:22px;background:#fff;font-size:10.5px;color:#555;display:flex;align-items:center;gap:5px;padding:0 7px}
.lang-box{width:12px;height:8px;background:#8aa4c4}
.nav{left:0;top:90px;width:908px;height:41px;background:linear-gradient(#29c0d2,#19a3b8);display:flex;padding-left:69px}
.nav a{display:flex;align-items:center;justify-content:center;color:#fff;text-decoration:none;font-size:12.5px;border-right:1px solid rgba(0,0,0,.15);text-shadow:0 1px 1px rgba(0,0,0,.3)}
.nav a.active{background:#168ea3}
.hero{left:0;top:131px;width:908px;height:239px;background:linear-gradient(#1a5870,#0a2f42)}
.hero-art{left:88px;top:38px;width:320px;height:170px;border-radius:30px;background:radial-gradient(ellipse at 40% 45%,#f4f6f8 0,#d4dbe0 45%,rgba(20,70,90,0) 72%)}
.hero h1{left:437px;top:36px;width:400px;color:#fff;font-size:18.5px;line-height:27px;font-weight:700}
.hero p{left:437px;top:100px;width:400px;color:#fff;font-size:11.5px;line-height:17.5px}
.demo{left:437px;top:148px;width:126px;height:35px;background:#fff;border-radius:2px;display:flex;align-items:center;justify-content:center;gap:6px;font-size:16px;color:#333}
.demo b{font-weight:700}
.welcome-band{left:0;top:370px;width:908px;height:250px;background:linear-gradient(#eeeeee,#ffffff)}
h2{font-size:19px;font-weight:600;color:var(--red);line-height:22px}
.body-text{font-size:11.2px;line-height:17.4px}
.btn{display:flex;align-items:center;justify-content:center;color:#fff;font-size:12px;font-weight:600;background:linear-gradient(var(--orange-light),var(--orange));border-radius:2px;text-shadow:0 1px 1px rgba(0,0,0,.3)}
.video{left:599px;top:430px;width:241px;height:152px;background:linear-gradient(#2b4a63,#172c3d);border-radius:2px}
.rule{left:69px;top:613px;width:771px;height:1px;background:#c9c9c9}
.col-text{text-align:justify}
.software h2{color:var(--orange)}
.svc{display:flex;align-items:center;gap:16px;height:34px;margin-bottom:1.5px;background:#ececec;border:1px solid #dcdcdc;padding-left:14px;color:var(--link);font-size:14.5px;font-weight:600}
.svc-arrow{width:16px;height:16px;background:#fff;border:1px solid #d0d0d0;display:flex;align-items:center;justify-content:center}
.blog-band{left:0;top:905px;width:908px;height:209px;background:#eeeeee}
.blog-img{left:69px;top:957px;width:241px;height:136px;background:radial-gradient(circle at 50% 40%,#3f7fe0,#0c2a8a 55%,#061442)}
.post-title{left:334px;top:954px;font-size:14px;color:var(--link)}
.post-meta{left:334px;top:975px;font-size:9.5px;color:#333}
.post-text{left:334px;top:996px;width:507px;font-size:11.2px;line-height:17.4px;text-align:justify}
.share{left:333px;top:1077px;display:flex;gap:6px;font-size:8.5px;align-items:center}
.share span{border:1px solid #c4c4c4;background:#f7f7f7;padding:1px 4px;border-radius:2px}
.footer{left:0;top:1114px;width:908px;height:86px;background:#2b2b2b}
.foot-links{left:69px;top:1136px;font-size:11.5px;color:#e0e0e0;display:flex;gap:10px}
.copy{left:69px;top:1163px;font-size:11px;color:#cfcfcf}
.social{top:1150px;width:18px;height:18px;border-radius:3px}
</style>
</head>
<body>
<header class="abs header"></header>
<div class="abs brand"><span class="brand-dot"></span>Velmarq Studio</div>
<div class="abs search">Search
<svg width="12" height="12" viewBox="0 0 12 12"><circle cx="5" cy="5" r="3.6" fill="none" stroke="#222" stroke-width="1.8"/><line x1="7.5" y1="7.5" x2="11" y2="11" stroke="#222" stroke-width="2.2"/></svg></div>
<div class="abs lang"><span class="lang-box"></span>Eng<svg width="7" height="5" viewBox="0 0 7 5" style="margin-left:auto"><path d="M0 0h7L3.5 5z" fill="#555"/></svg></div>

<nav class="abs nav">
  <a class="active" style="width:58px">Home</a>
  <a style="width:222px">Software Training and Implementation</a>
  <a style="width:133px">Project Management</a>
  <a style="width:154px">Business Process Analysis</a>
  <a style="width:49px">Blog</a>
  <a style="width:80px">About Us</a>
  <a style="width:75px">Contact Us</a>
</nav>

<section class="abs hero">
  <div class="abs hero-art" role="img" aria-label="Illustration of a white cloud beside a rising bar chart"></div>
  <h1 class="abs">Curabitur non massa vestibulum, egestas velit vitae, imperdiet velit.</h1>
  <p class="abs">Aliquam interdum sollicitudin odio. Mauris nunc ante, sagittis id porta quis, semper non neque. Suspendisse ac pulvinar tellus.</p>
  <div class="abs demo"><span><b>FREE</b> Demo</span>
    <svg width="18" height="18" viewBox="0 0 18 18"><circle cx="9" cy="9" r="9" fill="#777"/><path d="M7 5l4 4-4 4" stroke="#fff" stroke-width="2" fill="none"/></svg></div>
</section>

<div class="abs welcome-band"></div>
<h2 class="abs" style="left:69px;top:393px">Welcome to Velmarq Studio</h2>
<div class="abs body-text" style="left:69px;top:428px;width:504px">
  <p style="margin-bottom:6px">Cloud computing spending is due to account for a third of annual IT expenditure growth by the end of 2013. Every year the range of cloud software systems gets bigger, now including Brindlepath Accounting, Cloudmere Apps for Business, Jobvane Job Management Software, Deskpoint 365, Taskmoor Project Manager and many more.</p>
  <p>Signing up for cloud software is only the first part of the process, and then it has to be implemented into your business. That’s where Velmarq Studio comes in.</p>
</div>
<div class="abs btn" style="left:69px;top:553px;width:81px;height:29px">VIEW MORE</div>
<div class="abs video" role="img" aria-label="Video still of an open hand beneath a drawn cloud">
  <svg class="abs" style="left:92px;top:48px" width="56" height="56" viewBox="0 0 56 56"><circle cx="28" cy="28" r="25" fill="none" stroke="#fff" stroke-width="4"/><path d="M22 16l18 12-18 12z" fill="#fff"/></svg>
</div>
<div class="abs rule"></div>

<section class="abs" style="left:69px;top:640px;width:241px">
  <h2>Project Management</h2>
  <p class="body-text col-text" style="margin-top:12px">Project Management is one of the most important areas of any business operations, however can often be overlooked. Velmarq Studio can be engaged to help where project management is required but the resources are not available internally. Available for anything from half day reviews to several month projects, Velmarq Studio can be used as an outsourced resource to take out the pain of your project.</p>
</section>
<div class="abs btn" style="left:69px;top:844px;width:89px;height:30px">CONTACT US</div>

<section class="abs" style="left:334px;top:640px;width:241px">
  <h2>Business Process Analysis</h2>
  <p class="body-text col-text" style="margin-top:12px">Too often, small businesses spend plenty of time reviewing their market, and analysing competitior behaviour, but without ever taking a look inside their own operations. Velmarq Studio have experience with business reviews, marketing development, profit and loss analysis and much more, and can be engaged on anything from a half day review meeting to several months.</p>
</section>
<div class="abs btn" style="left:334px;top:844px;width:89px;height:30px">CONTACT US</div>

<section class="abs software" style="left:599px;top:640px;width:241px">
  <h2>Software Training and Implementation</h2>
  <div style="margin-top:16px">
    <div class="svc"><span class="svc-arrow"><svg width="6" height="8" viewBox="0 0 6 8"><path d="M1 1l3 3-3 3" stroke="#555" stroke-width="1.4" fill="none"/></svg></span>Brindlepath</div>
    <div class="svc"><span class="svc-arrow"><svg width="6" height="8" viewBox="0 0 6 8"><path d="M1 1l3 3-3 3" stroke="#555" stroke-width="1.4" fill="none"/></svg></span>Fieldwren</div>
    <div class="svc"><span class="svc-arrow"><svg width="6" height="8" viewBox="0 0 6 8"><path d="M1 1l3 3-3 3" stroke="#555" stroke-width="1.4" fill="none"/></svg></span>Cloudmere Apps</div>
    <div class="svc"><span class="svc-arrow"><svg width="6" height="8" viewBox="0 0 6 8"><path d="M1 1l3 3-3 3" stroke="#555" stroke-width="1.4" fill="none"/></svg></span>Stockhollow</div>
    <div class="svc"><span class="svc-arrow"><svg width="6" height="8" viewBox="0 0 6 8"><path d="M1 1l3 3-3 3" stroke="#555" stroke-width="1.4" fill="none"/></svg></span>Tillbright</div>
  </div>
</section>

<section class="abs blog-band"></section>
<h2 class="abs" style="left:69px;top:918px">Blog</h2>
<svg class="abs" style="left:817px;top:922px" width="24" height="14" viewBox="0 0 24 14"><path d="M8 2L3 7l5 5M16 2l5 5-5 5" stroke="#555" stroke-width="2.4" fill="none"/></svg>
<div class="abs blog-img" role="img" aria-label="Blue digital cloud with circuit lines over a dotted world map"></div>
<div class="abs post-title">Atullam volutpat dui et nisl pharetra, in convallis ipsum</div>
<div class="abs post-meta">July-31-13 &nbsp;:: &nbsp;10.15 a.m</div>
<p class="abs post-text">Pellentesque at tristique nunc. Nunc quam orci, egestas et tortor et, molestie adipiscing velit. Nunc hendrerit risus ut dui condimentum dignissim. Sed nec mattis augue. Nunc ante eros, eleifend ac odio id, dictum sagittis urna. Praesent eros dolor, condimentum ac laoreet id, laoreet vel sapien. Duis laoreet ac turpis eu molestie. Fusce facilisis nunc at orci congue aliquet.</p>
<div class="abs share"><span>Like</span><span>3k</span><span style="margin-left:4px">Share</span><span>316</span></div>

<footer class="abs footer"></footer>
<div class="abs foot-links"><span>Home</span><span>|</span><span>Software Training and Implementation</span><span>|</span><span>Project Management</span><span>|</span><span>Business Process Analysis</span><span>|</span><span>Blog</span><span>|</span><span>About Us</span><span>|</span><span>Contact Us</span></div>
<div class="abs copy">Copyright &nbsp;© &nbsp;2013 &nbsp;&nbsp;Velmarq Studio. &nbsp;&nbsp;&nbsp;All rights reserved.</div>
<div class="abs social" style="left:799px;background:#3b5a9a"></div>
<div class="abs social" style="left:823px;background:#3fb1e0"></div>
</body>
</html>
```